San Francisco Leading Consulting firm - 47Vora Web Design Project

•Create a Web Design
•Uncoded webpage layout design
•2 Pages Design - Homepage + Interior Page

Task Description
Hello, we're looking for a re-design our current website www.47vora-example.com

we have a sample mockup design @

http://47vora.pubtrellis-example.org/

This shows the layout that we like and also a sample of 6 pictures that would change based on where you mouse over..

6 pictures HOME design needs to be included.

SMART
THOUGHTFUL
FLEXIBLE
CREATIVE SERVICES
TECHNICAL SERVICES
PARTNERS

sites we like:

http://www.melvanadvisory-example.com/Home.cfm?id=Home
http://www.plinthworks-example.com/index.html

Our company can be best described as: 100+ employees, cutting-edge, depandable, innovative, strong, smart.

Our Primary focus is: IT Consulting Services and Creative Design services

47Vora LLC is a consulting firm providing creative design, business and technology solutions to both private and public interests.

Established in 1996, 47Vora is a San Francisco based company providing specialists for a range of business needs including:

Creative Design Services
•Print
•Logo Design
•Website Design
•Illustration

and

Business and Technology solutions

•Application Software and Web Development
•Business Process Re-Design (BPR)
•Business/Systems Analysis and Requirement Documentation
•Mentoring and Training
•Network/Hardware Installation Services
•System Design and Architecture
•Vendor Management
•Docuvault Architecture and Implementation

our sample mockup site:

Reason: Due to holiday season, we're not available to work with designers and finilize our design.  

Thank you very much for submitting your design.

We appreciate your time and creativity.   Since, our office is currently closed for holidays, we will be reviewing it in details next week and will make our decision as soon as possible.

It would be great if you could submit any of your changes by Wed next week, so it would be part of our reviews. 

Please see updated wireframe under attachments:  we have some minor updates to our wireframe that we would like you to update your designs, if possible.  

We also encorouge you not to use our standard wireframe and come up with more unique designs.   Everything would be considered when we review your design.

 

Target Market(s)

Creative services and professional services clients, including government agencies

Industry/Entity Type

Business

Requirements
Must have
• Clean, professional look, easy navigation

```html
<!DOCTYPE html>
<html lang="en">
<head>
<meta charset="utf-8">
<title>47Vora — Technology Solutions for the 21st Century</title>
<link rel="stylesheet" href="https://fonts.googleapis.com/css2?family=Arimo:wght@400;700&family=Questrial&display=swap">
<style>
:root{
  --bg:#e8e8e8;
  --page:#f1f1f1;
  --header:#f7f7f7;
  --footer-band:#f6f6f6;
  --ink:#3a3a3a;
  --muted:#6d6d6d;
  --faint:#b9b9b9;
  --orange:#f39a1f;
  --blue:#39b4ea;
  --blue-light:#7fd6fb;
  --green:#b5d66a;
  --rule:#dcdcdc;
}
*{box-sizing:border-box;margin:0;padding:0}
html,body{width:1200px;height:1134px;overflow:hidden}
body{background:radial-gradient(ellipse at 50% 40%,#fdfdfd 0%,#efefef 55%,var(--bg) 100%);font-family:"Arimo",Arial,sans-serif;color:var(--ink);position:relative}
.abs{position:absolute}

.site-header{left:170px;top:0;width:857px;height:91px;background:linear-gradient(#fdfdfd,var(--header));box-shadow:0 2px 6px rgba(0,0,0,.08)}
.brand{left:28px;top:26px;display:flex;align-items:center;gap:8px;font-family:"Questrial",sans-serif;font-size:24px;letter-spacing:1px;color:#2d4d6e}
.brand-dot{width:22px;height:22px;border-radius:50%;background:#2e8fd0}
.brand-rule{left:184px;top:36px;width:1px;height:46px;background:var(--rule)}
.tagline{left:192px;top:66px;font-size:10.5px;color:var(--faint)}
.search{left:726px;top:15px;width:135px;height:21px;background:#fff;border:1px solid #e1e1e1;font-size:7px;color:#aaa;padding:6px 7px;letter-spacing:.3px}
.search svg{position:absolute;right:4px;top:4px}
.home-icon{left:838px;top:68px}

.page{left:161px;top:91px;width:875px;height:978px;background:var(--page);box-shadow:0 0 10px rgba(0,0,0,.12)}

.main-nav{left:-5px;top:22px;width:178px;height:224px;background:#e6e6e6}
.nav-item{position:absolute;left:0;display:flex;align-items:center;gap:14px;font-size:10px;font-weight:700;letter-spacing:1px;color:#4a4a4a}
.nav-item .chev{color:var(--orange);font-size:13px;margin-left:-8px}
.nav-icon{width:33px;height:33px;background:linear-gradient(135deg,var(--blue-light),var(--blue));display:flex;align-items:center;justify-content:center;border-top-left-radius:3px}
.nav-icon.green{background:linear-gradient(135deg,#d3ea9b,var(--green))}

.welcome-title{left:192px;top:12px;font-family:"Questrial",sans-serif;font-size:30px;color:#cfcfcf}
.intro{left:196px;top:51px;width:660px;font-size:11.3px;line-height:21px;color:#444}
.intro p+p{margin-top:20px}

.showcase{left:189px;top:156px;width:691px;height:342px;background:#fff;box-shadow:0 1px 5px rgba(0,0,0,.25)}
.thumbs{left:4px;top:4px;width:102px;height:334px;background:#fff;box-shadow:2px 0 5px rgba(0,0,0,.2)}
.thumb{position:absolute;left:8px;width:88px;height:48px}
.thumb.active{box-shadow:4px 0 0 var(--orange)}
.hero{left:112px;top:4px;width:571px;height:329px;background:linear-gradient(180deg,#eef1f4 0%,#c9ccd1 45%,#7c7f86 75%,#5c5f65 100%)}
.hero-caption{left:0;top:219px;width:571px;height:44px;background:rgba(235,235,235,.85);font-family:"Questrial",sans-serif;font-size:33px;color:#222;padding:2px 0 0 32px}
.hero-next{right:0;top:92px;width:18px;height:30px;background:#8a8a8a;color:#fff;font-size:16px;text-align:center;line-height:30px}

.feature{top:532px;width:250px}
.feature h2{font-family:"Questrial",sans-serif;font-weight:400;font-size:17px;color:#555;margin-bottom:10px}
.feature h2 span{color:var(--orange);margin-right:6px}
.feature .visual{height:77px;position:relative}
.feature .visual b{position:absolute;left:10px;bottom:4px;font-size:11px;letter-spacing:.5px;color:#fff;line-height:15px}
.feature p{margin-top:20px;font-size:11.3px;line-height:22.5px;color:#6a6a6a;width:265px}
.btn{position:absolute;width:72px;height:27px;border-radius:3px;background:linear-gradient(var(--blue-light),var(--blue));color:#fff;font-size:10.5px;text-align:center;line-height:27px;box-shadow:0 2px 3px rgba(0,0,0,.2)}
.col-rule{top:546px;width:1px;height:240px;background:var(--rule)}

.services{left:0;top:810px;width:875px;height:168px;background:var(--footer-band);border-top:1px solid #e2e2e2}
.services h3{position:absolute;top:20px;font-size:12px;font-weight:700;color:#444}
.services ul{position:absolute;top:50px;list-style:none;font-size:9.3px;color:#333}
.services li{margin-bottom:11px;padding-left:9px;text-indent:-9px;line-height:12px}
.services li::before{content:"• "}

.site-footer{left:170px;top:1073px;width:857px;height:46px;background:#e4e4e4;font-size:9.5px;color:#666;padding:20px 0 0 14px}
</style>
</head>
<body>

<header class="site-header abs">
  <div class="brand abs"><span class="brand-dot"></span>47VORA</div>
  <div class="brand-rule abs"></div>
  <div class="tagline abs">Thechnology Solutions for the 21st Century</div>
  <div class="search abs">SEARCH ON THIS SITE
    <svg width="12" height="12" viewBox="0 0 12 12"><circle cx="7" cy="5" r="3.5" fill="none" stroke="#f39a1f" stroke-width="1.4"/><line x1="4.5" y1="7.5" x2="1.5" y2="10.5" stroke="#f39a1f" stroke-width="1.6"/></svg>
  </div>
  <svg class="home-icon abs" width="14" height="12" viewBox="0 0 14 12"><path d="M7 0 L14 6 H12 V12 H8.5 V8 H5.5 V12 H2 V6 H0 Z" fill="#8f8f8f"/></svg>
</header>

<main class="page abs">
  <nav class="main-nav abs">
    <div class="nav-item" style="top:7px"><span class="nav-icon"><svg width="16" height="16" viewBox="0 0 16 16"><path d="M2 14 L14 2 M5 14 L14 5 M2 11 L11 2" stroke="#fff" stroke-width="1.3"/></svg></span>COMPANY <span class="chev">›</span></div>
    <div class="nav-item" style="top:51px"><span class="nav-icon"><svg width="16" height="16" viewBox="0 0 16 16"><path d="M3 13 L10 6" stroke="#fff" stroke-width="2.5"/><circle cx="11.5" cy="4.5" r="3" fill="none" stroke="#fff" stroke-width="1.5"/></svg></span>TECHNICAL SERVICES <span class="chev">›</span></div>
    <div class="nav-item" style="top:94px"><span class="nav-icon"><svg width="16" height="16" viewBox="0 0 16 16"><circle cx="8" cy="6" r="4" fill="#fff"/><rect x="6" y="10" width="4" height="4" fill="#fff"/></svg></span>CREATIVE SERVICES <span class="chev">›</span></div>
    <div class="nav-item" style="top:137px"><span class="nav-icon"><svg width="18" height="14" viewBox="0 0 18 14"><path d="M1 7 L6 3 L12 8 L17 4 M6 3 L9 10" stroke="#fff" stroke-width="2" fill="none"/></svg></span>PARTNERS <span class="chev">›</span></div>
    <div class="nav-item" style="top:180px"><span class="nav-icon green"><svg width="16" height="14" viewBox="0 0 16 14"><circle cx="5" cy="4" r="2.5" fill="#fff"/><circle cx="11" cy="4" r="2.5" fill="#fff"/><path d="M1 13 Q5 6 9 13 Z M7 13 Q11 6 15 13 Z" fill="#fff"/></svg></span>CONTACT US</div>
  </nav>

  <h1 class="welcome-title abs">welcome</h1>
  <div class="intro abs">
    <p>47Vora LLC is a consulting firm providing creative design, business and technology solutions to both private and public interests.</p>
    <p>Our experts possess broad industry knowledge which can help with technical and business process challenges, delivering solutions that are creative and cost effective.</p>
  </div>

  <section class="showcase abs">
    <div class="thumbs abs">
      <div class="thumb" role="img" aria-label="Puzzle pieces with business people" style="top:6px;background:linear-gradient(#f4f4f4,#9a9a9a)"></div>
      <div class="thumb" role="img" aria-label="Person working at a laptop" style="top:60px;background:linear-gradient(#8d7c6a,#3d3630)"></div>
      <div class="thumb" role="img" aria-label="Figure leaping against a sky" style="top:114px;background:linear-gradient(#3c95c4,#6bbf4e)"></div>
      <div class="thumb" role="img" aria-label="Coloured markers" style="top:168px;background:linear-gradient(135deg,#2b2b2b,#d04a8a,#79b83b)"></div>
      <div class="thumb active" role="img" aria-label="Business team standing together" style="top:222px;background:linear-gradient(#d9d9d9,#3a3a3a)"></div>
      <div class="thumb" role="img" aria-label="Figure facing a blue screen" style="top:276px;background:linear-gradient(#1d5fa7,#0d2a4e)"></div>
    </div>
    <div class="hero abs" role="img" aria-label="Business people meeting on a busy footbridge">
      <div class="hero-caption abs">technical services</div>
      <div class="hero-next abs">›</div>
    </div>
  </section>

  <article class="feature abs" style="left:17px">
    <h2><span>›</span>for graphic designers</h2>
    <div class="visual" role="img" aria-label="Colourful creative head artwork with a pink swoosh" style="width:204px;background:linear-gradient(90deg,#7a2a8c 0%,#c45bb0 35%,#f3d6e6 70%,#f1f1f1 100%)"><b style="left:75px;top:12px;bottom:auto;color:#6d1c84">GET<br>CREATIVE !</b></div>
    <p>47Vora is looking for top creative talent to deliver graphic design solutions for some leading global brands Do you have what it takes?</p>
  </article>
  <a class="btn" style="left:204px;top:754px">Learn More</a>
  <div class="col-rule abs" style="left:289px"></div>

  <article class="feature abs" style="left:313px">
    <h2><span>›</span>for clients</h2>
    <div class="visual" role="img" aria-label="Red figure running with a briefcase among grey figures" style="width:242px;background:linear-gradient(90deg,#9d9d9d,#c8c8c8 50%,#8a8a8a)"><b style="left:auto;right:6px;text-align:right">THE 47VORA<br>DIFFERENCE</b></div>
    <p>Smart, Flexible, Thoughtful: find out why leading corporations and government agencies are turning to 47Vora to help manage their most demanding IT services challenges.</p>
  </article>
  <a class="btn" style="left:502px;top:754px">Learn More</a>
  <div class="col-rule abs" style="left:586px"></div>

  <article class="feature abs" style="left:611px">
    <h2><span>›</span>for partners</h2>
    <div class="visual" role="img" aria-label="Business handshake" style="width:242px;background:linear-gradient(90deg,#1d1d1d,#6c6c6c 50%,#2a2a2a)"><b>TEAM UP<br>WITH THE BEST</b></div>
    <p>When it comes to technology partnerships, our mission it so make you a success.</p>
  </article>
  <a class="btn" style="left:789px;top:754px">Learn More</a>

  <section class="services abs">
    <h3 style="left:25px">Creative Design Services</h3>
    <ul style="left:36px"><li>Print</li><li>Logo Design</li><li>Website Design</li><li>Illustration</li></ul>
    <h3 style="left:315px">Business and Technology solutions</h3>
    <ul style="left:328px;width:210px"><li>Application Software and Web Development</li><li>Business Process Re-Design (BPR)</li><li>Business/Systems Analysis and Requirement Documentation</li><li>Mentoring and Training</li></ul>
    <ul style="left:563px;width:240px"><li>Network/Hardware Installation Services</li><li>System Design and Architecture</li><li>Vendor Management</li><li>Docuvault Architecture and Implementation</li></ul>
  </section>
</main>

<footer class="site-footer abs">Copyright 2010, 47Vora, LLC All rights reserved.</footer>

</body>
</html>
```